BOLD & MINIMALIST DESIGN NEEDED

We want a very bold but minimalistic business card design that is impactful and utilizes both sides of the business card. Our current logo is included for your use.

We want bold fonts and good use of negative space. We don't want the logo to overpower the design.

Target Market(s)

Professionals who are building new commercial buildings.

Industry/Entity Type

Construction

Contact Information for Business Card

Name, Title, email, office phone, cell phone, website

Font styles to use
Serif
Sans Serif

Requirements
Must have
• Bold design!

```html
<!DOCTYPE html>
<html lang="en">
<head>
<meta charset="utf-8">
<title>Ridgeline Build – Business Card</title>
<link rel="stylesheet" href="https://fonts.googleapis.com/css2?family=Montserrat:wght@400;500;800&display=swap">
<style>
  :root {
    --backdrop: #949494;
    --card: #ffffff;
    --ink: #0c0c0e;
    --green: #7cc242;
    --shadow: rgba(0, 0, 0, 0.35);
  }
  * { margin: 0; padding: 0; box-sizing: border-box; }
  html, body {
    width: 1200px; height: 1200px; overflow: hidden;
    background: var(--backdrop);
    font-family: "Montserrat", sans-serif;
    color: var(--ink);
  }
  .stage { position: relative; width: 1200px; height: 1200px; }
  .card {
    position: absolute; left: 180px; width: 867px; height: 499px;
    background: var(--card);
    box-shadow: 0 14px 26px var(--shadow);
    overflow: hidden;
  }
  .card--front { top: 85px; }
  .card--back { top: 625px; }

  .brand {
    display: flex; align-items: center; gap: 14px;
    font-weight: 800; letter-spacing: 1px; text-transform: uppercase;
    color: var(--ink);
  }
  .brand__mark { background: var(--green); flex: none; }
  .card--front .brand {
    position: absolute; left: 0; right: 0; top: 218px;
    justify-content: center; font-size: 54px; gap: 18px;
  }
  .card--front .brand__mark { width: 44px; height: 44px; }
  .card--back .brand {
    position: absolute; left: 36px; top: 37px; font-size: 44px;
  }
  .card--back .brand__mark { width: 34px; height: 34px; }

  .person { position: absolute; left: 36px; top: 170px; }
  .person__accent {
    position: absolute; left: -36px; top: 8px;
    width: 5px; height: 61px; background: var(--ink);
  }
  .person__name { font-weight: 800; font-size: 34px; line-height: 1.1; letter-spacing: 0.5px; }
  .person__title { font-weight: 400; font-size: 29px; line-height: 1.2; color: var(--green); letter-spacing: 1px; }

  .contacts { position: absolute; left: 36px; top: 340px; list-style: none; }
  .contacts li {
    display: flex; align-items: center; height: 35px;
    font-size: 22px; font-weight: 400; letter-spacing: 1px;
  }
  .contacts svg { width: 25px; height: 25px; margin-right: 12px; flex: none; }

  .corner-block {
    position: absolute; left: 631px; top: 303px; width: 196px; height: 196px;
    background: var(--green);
    border-bottom: 22px solid var(--ink);
  }
</style>
</head>
<body>
<main class="stage">
  <section class="card card--front" aria-label="Card front">
    <div class="brand"><span class="brand__mark"></span>Ridgeline Build</div>
  </section>

  <section class="card card--back" aria-label="Card back">
    <div class="brand"><span class="brand__mark"></span>Ridgeline Build</div>

    <div class="person">
      <span class="person__accent"></span>
      <p class="person__name">Name Surename</p>
      <p class="person__title">Director</p>
    </div>

    <ul class="contacts">
      <li>
        <svg viewBox="0 0 24 24" aria-hidden="true"><path fill="#0c0c0e" d="M6.6 10.8a15 15 0 0 0 6.6 6.6l2.2-2.2c.3-.3.7-.4 1-.2 1.1.4 2.3.6 3.6.6.6 0 1 .4 1 1V20c0 .6-.4 1-1 1A17 17 0 0 1 3 4c0-.6.4-1 1-1h3.5c.6 0 1 .4 1 1 0 1.3.2 2.5.6 3.6.1.3 0 .7-.2 1z"/></svg>
        555-014-2200
      </li>
      <li>
        <svg viewBox="0 0 24 24" aria-hidden="true"><path fill="#0c0c0e" d="M2 8c0-2 4-4 10-4s10 2 10 4v2h-5V8H7v2H2zm5 3h10l3 5v4H4v-4zm5 2a2 2 0 1 0 0 4 2 2 0 0 0 0-4z"/></svg>
        555-014-2200
      </li>
      <li>
        <svg viewBox="0 0 24 24" aria-hidden="true"><path fill="#0c0c0e" d="M2 5h20v14H2zm2 2v.3l8 6 8-6V7zm0 2.8V17h16V9.8l-8 6z"/></svg>
        info@ridgelinebuild.com
      </li>
      <li>
        <svg viewBox="0 0 24 24" aria-hidden="true"><g fill="none" stroke="#0c0c0e" stroke-width="1.6"><circle cx="12" cy="12" r="10"/><ellipse cx="12" cy="12" rx="4.5" ry="10"/><path d="M2 12h20M4 6.5h16M4 17.5h16M12 2v20"/></g></svg>
        www.ridgelinebuild.com
      </li>
    </ul>

    <div class="corner-block" aria-hidden="true"></div>
  </section>
</main>
</body>
</html>
```